Need a Zine cover designed

I’m looking for someone who can design an eye catching and original zine cover. Incorporating the logo I included below. I’m not 100% sure which logo I want to use on the cover, if it’s possible to see how you incorporate the logos on a sample will make it easier for me to decide. Thank you for your time.
For the second logo I’m unsure how to remove the grey background, but I do not want it included in the zine cover
The title of the zine is:
Marigold Crossing
perspectives of culture, life, & love

```html
<!DOCTYPE html>
<html lang="en">
<head>
<meta charset="utf-8">
<title>Marigold Crossing — Zine Cover</title>
<link href="https://fonts.googleapis.com/css2?family=Bungee&family=Lobster&family=Montserrat:wght@800&display=swap" rel="stylesheet">
<style>
  :root {
    --backdrop: #a3a4a7;
    --kraft: #d8b49c;
    --kraft-light: #e2c3ad;
    --kraft-spine: #caa48b;
    --fold: rgba(120, 85, 65, 0.28);
    --fold-light: rgba(255, 240, 225, 0.35);
    --ink-red: #c0221f;
  }
  * { margin: 0; padding: 0; box-sizing: border-box; }
  html, body {
    width: 1176px;
    height: 1200px;
    overflow: hidden;
    background: var(--backdrop);
  }
  .stage {
    width: 1176px;
    height: 1200px;
    display: flex;
    align-items: center;
    justify-content: center;
  }
  .zine-cover {
    position: relative;
    width: 820px;
    height: 1130px;
    background: radial-gradient(ellipse at 50% 40%, var(--kraft-light), var(--kraft) 75%);
    overflow: hidden;
  }
  .spine-band {
    position: absolute;
    left: 0; top: 0; bottom: 0;
    width: 58px;
    background: var(--kraft-spine);
    border-right: 2px solid var(--fold);
  }
  .fold-lines {
    position: absolute;
    inset: 0;
  }
  .club-name {
    position: absolute;
    top: 170px;
    left: 150px;
    width: 420px;
    text-align: center;
    font-family: "Montserrat", sans-serif;
    font-weight: 800;
    font-size: 52px;
    line-height: 1.05;
    color: var(--ink-red);
  }
  .zine-title {
    position: absolute;
    top: 430px;
    left: 90px;
    width: 680px;
    text-align: center;
    font-family: "Bungee", sans-serif;
    color: var(--ink-red);
    line-height: 0.95;
  }
  .zine-title .line-one { display: block; font-size: 104px; }
  .zine-title .line-two { display: block; font-size: 96px; }
  .tagline {
    position: absolute;
    top: 900px;
    left: 120px;
    width: 640px;
    text-align: center;
    color: var(--ink-red);
  }
  .tagline .kicker {
    display: block;
    font-family: "Montserrat", sans-serif;
    font-weight: 800;
    font-size: 26px;
    letter-spacing: 0.32em;
  }
  .tagline .script {
    display: block;
    margin-top: 2px;
    font-family: "Lobster", cursive;
    font-size: 88px;
    line-height: 1.05;
  }
</style>
</head>
<body>
  <main class="stage">
    <section class="zine-cover">
      <div class="spine-band"></div>
      <svg class="fold-lines" width="820" height="1130" viewBox="0 0 820 1130" aria-hidden="true">
        <line x1="58" y1="300" x2="820" y2="300" stroke="var(--fold)" stroke-width="2"/>
        <line x1="58" y1="302" x2="820" y2="302" stroke="var(--fold-light)" stroke-width="2"/>
        <line x1="58" y1="590" x2="820" y2="590" stroke="var(--fold)" stroke-width="2"/>
        <line x1="58" y1="592" x2="820" y2="592" stroke="var(--fold-light)" stroke-width="2"/>
        <line x1="58" y1="840" x2="820" y2="840" stroke="var(--fold)" stroke-width="2"/>
        <line x1="58" y1="842" x2="820" y2="842" stroke="var(--fold-light)" stroke-width="2"/>
        <line x1="439" y1="0" x2="439" y2="1130" stroke="var(--fold)" stroke-width="1.5" opacity="0.6"/>
      </svg>

      <div class="club-name">Mellow Hours<br>Club</div>

      <h1 class="zine-title">
        <span class="line-one">Marigold</span>
        <span class="line-two">Crossing</span>
      </h1>

      <p class="tagline">
        <span class="kicker">PERSPECTIVES OF LIFE</span>
        <span class="script">Culture &amp; Love</span>
      </p>
    </section>
  </main>
</body>
</html>
```